Business Card and Simple Logo Desgin

New Zealand based start up company "Vesta Advisory LTD" requires business cards and simple logo design.

Card Content.

Vesta Advisory LTD

Rebecca Thornbury
CA, BMS (Hons)

r.thornbury@vestaadvisory.co.nz
PH +64 21 574 613

Target Market(s)

Corporate Business in IT, Finance and accounting.

Industry/Entity Type

Business

```html
<!DOCTYPE html>
<html lang="en">
<head>
<meta charset="utf-8">
<title>Vesta Advisory LTD — Business Card</title>
<link rel="stylesheet" href="https://fonts.googleapis.com/css2?family=Didact+Gothic&display=swap">
<style>
  :root {
    --backdrop: #2b2b2b;
    --card-light: #ffffff;
    --card-shade: #dcdcdc;
    --ink: #2a2a2a;
    --ink-soft: #4a4a4a;
    --divider: #6e6e6e;
    --accent: #f07a2a;
    --band: #0c0c0c;
    --band-text: #f2f2f2;
    --bubble-tone: #c9c9c9;
  }
  html, body {
    margin: 0;
    width: 1200px;
    height: 900px;
    overflow: hidden;
    background: var(--backdrop);
    font-family: "Didact Gothic", "Century Gothic", sans-serif;
  }
  .canvas {
    position: relative;
    width: 1200px;
    height: 900px;
  }
  .card {
    position: absolute;
    left: 100px;
    top: 164px;
    width: 1000px;
    height: 572px;
    background: linear-gradient(160deg, var(--card-light) 0%, #f4f4f4 45%, var(--card-shade) 100%);
    box-shadow: 0 18px 40px rgba(0,0,0,0.55);
    overflow: hidden;
  }
  .bubble-field {
    position: absolute;
    left: 0;
    right: 0;
    bottom: 34px;
    height: 190px;
    background:
      radial-gradient(ellipse 30% 70% at 12% 100%, rgba(201,201,201,0.55), transparent 70%),
      radial-gradient(ellipse 35% 80% at 55% 100%, rgba(201,201,201,0.45), transparent 70%),
      radial-gradient(ellipse 22% 90% at 93% 60%, rgba(201,201,201,0.5), transparent 70%);
  }
  .brand {
    position: absolute;
    left: 70px;
    top: 258px;
    display: flex;
    align-items: center;
    gap: 12px;
  }
  .brand-dot {
    width: 16px;
    height: 16px;
    border-radius: 50%;
    background: var(--accent);
  }
  .brand-name {
    font-size: 38px;
    color: var(--ink);
    letter-spacing: 0.2px;
  }
  .divider {
    position: absolute;
    left: 530px;
    top: 200px;
    width: 4px;
    height: 150px;
    background: var(--divider);
  }
  .contact {
    position: absolute;
    left: 575px;
    top: 206px;
    color: var(--ink);
  }
  .contact-name {
    margin: 0;
    font-size: 27px;
    line-height: 1.05;
    font-weight: normal;
  }
  .contact-quals {
    margin: 0 0 0 6px;
    font-size: 27px;
    line-height: 1.05;
  }
  .contact-lines {
    margin: 26px 0 0 20px;
    font-size: 19px;
    line-height: 1.4;
    color: var(--ink-soft);
  }
  .web-band {
    position: absolute;
    left: 0;
    right: 0;
    bottom: 0;
    height: 34px;
    background: var(--band);
    color: var(--band-text);
    font-size: 21px;
    line-height: 34px;
    padding-left: 220px;
    letter-spacing: 0.4px;
  }
</style>
</head>
<body>
  <main class="canvas">
    <section class="card" aria-label="Vesta Advisory business card">
      <div class="bubble-field" role="img" aria-label="Soft grey bubble decoration along the lower edge"></div>

      <div class="brand">
        <span class="brand-name">Vesta Advisory LTD</span>
        <span class="brand-dot"></span>
      </div>

      <div class="divider"></div>

      <div class="contact">
        <h1 class="contact-name">Rebecca Thornbury</h1>
        <p class="contact-quals">CA, BMS (Hons)</p>
        <div class="contact-lines">
          <div class="contact-email">r.thornbury@vestaadvisory.co.nz</div>
          <div class="contact-phone">PH +64 21 574 613</div>
        </div>
      </div>

      <footer class="web-band">www.vestaadvisoryltd.co.nz</footer>
    </section>
  </main>
</body>
</html>
```